Elite Leadership Transformation Roadmap

I've included a mock up of what I like. This design needs to be made better. I like the top section layout. It needs 5 circles for:

Please create a webpage based on this design, but improve it. Use the letterhead and business card brand you created for me to make the brand look seamless.

I love the circles - please make 5 of them the same size (can be 1 lines)

Here is the text for the circles:

Headline: Your Guided Path to Transformation
Text
Step 1: The Initial Consultation
text
Step 2: Deep-Dive Discovery and Assessment
text
Step 3: Synthesis and Strategy Formulation
text
Step 4: The Strategic Debrief Session
Text
Step 5: Implementation and Ongoing Support
Text

Also, there are many sections to this page including:

Introduction
Copy
Copy
Bio
CTA
FAQ's

Please make it interesting.

Use the colors of the mockup and my website: Corwin Adeley.com
I am including my letterhead and business card for brand coherence.

Use the fonts on my website. CorwinAdeley.com

I will need all files to send to the developer. We must have ALL the art files.

see my website; CorwinAdeley.com

See my uploads

Must have
• all the design files

```html
<!DOCTYPE html>
<html lang="en">
<head>
<meta charset="utf-8">
<title>Corwin Adeley – Elite Leadership Coaching</title>
<link href="https://fonts.googleapis.com/css2?family=Arimo:wght@400;700&family=Open+Sans:wght@400;600;700&display=swap" rel="stylesheet">
<style>
:root{
  --navy:#21344d;
  --navy-deep:#1a2a40;
  --gold:#b48a52;
  --gold-dark:#8a6331;
  --gold-light:#e6c15f;
  --gold-pale:#d9b77e;
  --ink:#1b1b1b;
  --text:#3a3a3a;
  --muted:#8e8e8e;
  --cream:#f6f3ee;
  --black:#050505;
  --white:#ffffff;
}
*{box-sizing:border-box;margin:0;padding:0}
html,body{width:1200px;height:4532px;overflow:hidden}
body{position:relative;background:var(--white);font-family:"Open Sans",Arial,sans-serif;color:var(--text)}
.abs{position:absolute}
.heading{font-family:"Arimo",Arial,sans-serif;color:var(--ink);font-weight:400}
.heading b{font-weight:700}
.rule{width:46px;height:3px;background:var(--gold)}
.btn{position:absolute;display:flex;align-items:center;justify-content:center;border-radius:22px;background:linear-gradient(180deg,var(--gold),var(--gold-dark));color:#fff;font-weight:700;font-size:15px;box-shadow:0 2px 6px rgba(0,0,0,.2)}

/* header */
.site-header{top:0;left:0;width:1200px;height:83px;background:#fff;z-index:5;box-shadow:0 1px 4px rgba(0,0,0,.08)}
.brand{left:112px;top:0;height:83px;display:flex;align-items:center;gap:10px;font-family:"Arimo",Arial,sans-serif;font-weight:700;font-size:20px;color:var(--gold-dark)}
.brand-dot{width:34px;height:34px;border-radius:50%;background:var(--gold)}
.nav{left:563px;top:30px;display:flex;gap:24px;font-size:15px;color:#333}
.nav .active{color:var(--gold);font-weight:700}
.nav-contact{left:959px;top:20px;width:130px;height:42px}

/* hero */
.hero{top:83px;left:0;width:1200px;height:560px;background:linear-gradient(90deg,#2c4058,var(--navy) 60%,#1d3049)}
.hero-photo{left:0;top:0;width:600px;height:560px;background:radial-gradient(ellipse at 45% 40%,#6c5a52 0%,#3b3f4b 45%,rgba(33,52,77,0) 75%)}
.hero-title{left:618px;top:168px;color:#fff;font-size:43px;line-height:52px}
.hero-sub{left:618px;top:275px;width:440px;color:#e8eaef;font-size:15px;line-height:26px}
.hero-btn{left:618px;top:344px;width:202px;height:42px}
.hero-curve{top:520px;left:0;width:1200px;height:170px}

/* path */
.path-title{top:760px;left:0;width:1200px;text-align:center;font-size:30px}
.path-rule{top:803px;left:577px}
.step{top:850px;width:158px;height:158px}
.step-label{top:1027px;width:200px;text-align:center;font-size:14px;line-height:21px;color:#333}
.arrow{top:921px;width:44px;height:16px}

/* about */
.about{top:1156px;left:0;width:1200px;height:630px;background:linear-gradient(180deg,#f3efe8,#efe9df 60%,#e6dfd3)}
.about-art{left:132px;top:102px;width:432px;height:432px;border-radius:50%;background:radial-gradient(circle at 50% 45%,#fbf6ec 0%,#e9dcc3 55%,#c9a56b 78%,#a57a3f 80%,#f1ece3 82%)}
.about-title{left:637px;top:124px;font-size:32px}
.about-rule{left:637px;top:174px}
.about-copy{left:637px;top:196px;width:440px;font-size:14px;line-height:27.5px;color:#333}
.about-copy p+p{margin-top:27px}
.about-btn{left:637px;top:462px;width:134px;height:42px}

/* bio */
.bio{top:1786px;left:0;width:1200px;height:525px;background:linear-gradient(180deg,#b38c55 0%,#a57c45 55%,#946a36 100%)}
.bio-title{left:109px;top:88px;color:#fff;font-size:32px}
.bio-rule{left:109px;top:137px;background:#fff}
.bio-copy{left:109px;top:160px;width:490px;color:#fff;font-size:14px;line-height:26px}
.bio-copy p+p{margin-top:26px}
.bio-btn{left:109px;top:386px;width:134px;height:42px;background:#fff;color:var(--gold-dark)}
.bio-frame{left:664px;top:66px;width:396px;height:396px;border-radius:50%;background:linear-gradient(135deg,#d8b275,#7d5726);padding:16px}
.bio-photo{width:100%;height:100%;border-radius:50%;background:radial-gradient(circle at 50% 45%,#b59a86 0%,#3c4353 55%,#24324a 100%);border:6px solid #caa36a}

/* benefits */
.benefits-title{top:2394px;left:0;width:1200px;text-align:center;font-size:31px;line-height:42px}
.benefits-sub{top:2505px;left:200px;width:800px;text-align:center;font-size:15px;line-height:27px;color:#333}
.benefit{top:2586px;width:144px;height:144px}
.benefit-label{top:2744px;width:220px;text-align:center;font-family:"Arimo",Arial,sans-serif;font-weight:700;font-size:15px;line-height:26px;color:#222}

/* cta */
.cta{top:2874px;left:0;width:1200px;height:403px;background:radial-gradient(ellipse at 80% 50%,#2f3e55,var(--navy-deep) 70%)}
.cta-title{top:80px;left:0;width:1200px;text-align:center;color:#fff;font-size:31px;line-height:41px}
.cta-rule{top:167px;left:577px}
.cta-copy{top:198px;left:150px;width:900px;text-align:center;color:#fff;font-size:15px;line-height:28px}
.cta-btn{top:275px;left:498px;width:204px;height:42px}

/* faq */
.faq-title{top:3356px;left:0;width:1200px;text-align:center;font-size:31px;font-weight:700}
.faq-rule{top:3400px;left:577px}
.faq-item{left:162px;width:876px;height:46px;border-radius:14px;background:#fff;box-shadow:0 2px 10px rgba(0,0,0,.12);padding:0 30px;display:flex;align-items:center;justify-content:space-between;font-size:15px;color:#222}
.faq-open{height:116px;border:2px solid var(--gold-pale);align-items:flex-start;flex-direction:column;justify-content:flex-start;padding-top:14px}
.faq-open .answer{margin-top:12px;font-size:13.5px;line-height:21px;color:#777;width:720px}
.toggle{width:28px;height:28px;border-radius:50%;background:linear-gradient(180deg,var(--gold),var(--gold-dark));color:#fff;display:flex;align-items:center;justify-content:center;font-size:18px;font-weight:700;flex:none}
.faq-open .toggle{position:absolute;right:14px;top:10px}
.faq-btn{top:3797px;left:537px;width:126px;height:42px}

/* footer */
.footer-curve{top:3930px;left:0;width:1200px;height:140px}
.footer{top:4060px;left:0;width:1200px;height:472px;background:var(--black)}
.footer-brand{top:48px;left:0;width:1200px;display:flex;flex-direction:column;align-items:center;gap:10px;font-family:"Arimo",Arial,sans-serif;font-weight:700;font-size:24px;color:var(--gold)}
.footer-brand .brand-dot{width:52px;height:52px}
.footer-nav{top:174px;left:0;width:1200px;display:flex;justify-content:center;gap:48px;color:#fff;font-size:16px}
.footer-line{left:136px;width:936px;height:1px;background:#555}
.contact{top:290px;display:flex;gap:14px;color:#fff;font-size:15px;line-height:28px}
.contact strong{font-weight:700}
.contact-icon{width:40px;height:40px;border-radius:50%;background:linear-gradient(180deg,var(--gold),var(--gold-dark));display:flex;align-items:center;justify-content:center;flex:none}
.copyright{top:415px;left:198px;color:#fff;font-size:14px}
.social{top:406px;left:884px;display:flex;gap:9px}
.social span{width:33px;height:33px;border-radius:50%;background:linear-gradient(180deg,var(--gold),var(--gold-dark))}
</style>
</head>
<body>

<header class="abs site-header">
  <div class="abs brand"><span class="brand-dot"></span>Corwin Adeley</div>
  <nav class="abs nav"><span class="active">Home</span><span>Coaching</span><span>Retreats</span><span>About</span><span>Insights</span></nav>
  <div class="btn nav-contact">Contact Us</div>
</header>

<section class="abs hero">
  <div class="abs hero-photo" role="img" aria-label="Portrait photograph of the coach in a dark blazer"></div>
  <h1 class="abs heading hero-title" style="color:#fff">Elevate your leadership<br><b>with Elite Coaching.</b></h1>
  <p class="abs hero-sub">Introducing Elite Leadership Coaching and Organization Development</p>
  <div class="btn hero-btn">Book a Discovery Call</div>
</section>
<svg class="abs hero-curve" viewBox="0 0 1200 170" aria-hidden="true">
  <defs><linearGradient id="goldBand" x1="0" x2="1"><stop offset="0" stop-color="#8a6331"/><stop offset=".5" stop-color="#a57a3f"/><stop offset="1" stop-color="#d2ad6e"/></linearGradient></defs>
  <path d="M0 58 Q600 230 1200 48 L1200 170 L0 170Z" fill="#fff"/>
  <path d="M0 52 Q600 222 1200 42" fill="none" stroke="url(#goldBand)" stroke-width="16"/>
  <circle cx="600" cy="135" r="24" fill="#fff" stroke="#c9a36a" stroke-width="3"/>
</svg>

<!-- guided path -->
<h2 class="abs heading path-title"><b>Your Guided Path</b> to Transformation</h2>
<div class="abs rule path-rule"></div>

<svg class="abs step" style="left:111px" viewBox="0 0 158 158" aria-hidden="true"><circle cx="79" cy="79" r="69" fill="#fff" stroke="#e6c15f" stroke-width="18"/><path d="M10 79 A69 69 0 0 0 40 136" fill="none" stroke="#c9a046" stroke-width="18"/><circle cx="79" cy="14" r="14" fill="#b48a52"/><circle cx="79" cy="14" r="5" fill="#fff"/><text x="79" y="76" text-anchor="middle" font-family="Arimo,Arial,sans-serif" font-size="13" font-weight="700" fill="#b48a52">The Initial</text><text x="79" y="95" text-anchor="middle" font-family="Arimo,Arial,sans-serif" font-size="13" font-weight="700" fill="#b48a52">Consultation</text></svg>
<svg class="abs step" style="left:317px" viewBox="0 0 158 158" aria-hidden="true"><circle cx="79" cy="79" r="69" fill="#fff" stroke="#e6c15f" stroke-width="18"/><path d="M22 118 A69 69 0 0 0 79 148" fill="none" stroke="#c9a046" stroke-width="18"/><circle cx="79" cy="14" r="14" fill="#b48a52"/><circle cx="79" cy="14" r="5" fill="#fff"/><text x="79" y="74" text-anchor="middle" font-family="Arimo,Arial,sans-serif" font-size="13" font-weight="700" fill="#b48a52">Deep-Dive</text><text x="79" y="93" text-anchor="middle" font-family="Arimo,Arial,sans-serif" font-size="13" font-weight="700" fill="#b48a52">Discovery</text></svg>
<svg class="abs step" style="left:521px" viewBox="0 0 158 158" aria-hidden="true"><circle cx="79" cy="79" r="69" fill="#fff" stroke="#e6c15f" stroke-width="18"/><path d="M79 148 A69 69 0 0 0 128 128" fill="none" stroke="#c9a046" stroke-width="18"/><circle cx="79" cy="14" r="14" fill="#b48a52"/><circle cx="79" cy="14" r="5" fill="#fff"/><text x="79" y="74" text-anchor="middle" font-family="Arimo,Arial,sans-serif" font-size="13" font-weight="700" fill="#b48a52">Synthesis</text><text x="79" y="93" text-anchor="middle" font-family="Arimo,Arial,sans-serif" font-size="13" font-weight="700" fill="#b48a52">and Strategy</text></svg>
<svg class="abs step" style="left:725px" viewBox="0 0 158 158" aria-hidden="true"><circle cx="79" cy="79" r="69" fill="#fff" stroke="#e6c15f" stroke-width="18"/><path d="M128 128 A69 69 0 0 0 148 79" fill="none" stroke="#c9a046" stroke-width="18"/><circle cx="79" cy="14" r="14" fill="#b48a52"/><circle cx="79" cy="14" r="5" fill="#fff"/><text x="79" y="76" text-anchor="middle" font-family="Arimo,Arial,sans-serif" font-size="13" font-weight="700" fill="#b48a52">Strategic</text><text x="79" y="95" text-anchor="middle" font-family="Arimo,Arial,sans-serif" font-size="13" font-weight="700" fill="#b48a52">Debrief</text></svg>
<svg class="abs step" style="left:929px" viewBox="0 0 158 158" aria-hidden="true"><circle cx="79" cy="79" r="69" fill="#fff" stroke="#e6c15f" stroke-width="18"/><path d="M108 16 A69 69 0 0 1 142 52" fill="none" stroke="#c9a046" stroke-width="18"/><circle cx="79" cy="14" r="14" fill="#b48a52"/><circle cx="79" cy="14" r="5" fill="#fff"/><text x="79" y="74" text-anchor="middle" font-family="Arimo,Arial,sans-serif" font-size="12.5" font-weight="700" fill="#b48a52">Implementation</text><text x="79" y="93" text-anchor="middle" font-family="Arimo,Arial,sans-serif" font-size="13" font-weight="700" fill="#b48a52">Support</text></svg>

<svg class="abs arrow" style="left:272px" viewBox="0 0 44 16" aria-hidden="true"><path d="M2 8H40M34 3l6 5-6 5" fill="none" stroke="#bbb" stroke-width="1.5"/></svg>
<svg class="abs arrow" style="left:477px" viewBox="0 0 44 16" aria-hidden="true"><path d="M2 8H40M34 3l6 5-6 5" fill="none" stroke="#bbb" stroke-width="1.5"/></svg>
<svg class="abs arrow" style="left:681px" viewBox="0 0 44 16" aria-hidden="true"><path d="M2 8H40M34 3l6 5-6 5" fill="none" stroke="#bbb" stroke-width="1.5"/></svg>
<svg class="abs arrow" style="left:885px" viewBox="0 0 44 16" aria-hidden="true"><path d="M2 8H40M34 3l6 5-6 5" fill="none" stroke="#bbb" stroke-width="1.5"/></svg>

<p class="abs step-label" style="left:90px">Elite Coaching with<br>Corwin</p>
<p class="abs step-label" style="left:296px">Deep-Dive Discovery<br>and Assessment</p>
<p class="abs step-label" style="left:500px">Synthesis and Strategy<br>Formulation</p>
<p class="abs step-label" style="left:704px">The Strategic Debrief<br>Session</p>
<p class="abs step-label" style="left:908px">Implementation and<br>Ongoing Support</p>

<!-- about -->
<section class="abs about">
  <div class="abs about-art" role="img" aria-label="Large brand tree emblem in teal and gold within a gold ring"></div>
  <h2 class="abs heading about-title">About Us</h2>
  <div class="abs rule about-rule"></div>
  <div class="abs about-copy">
    <p>My mission is to guide high-performing leaders and their teams toward a state of peak performance defined by stress-free resilience, heightened productivity, and effortless flow.</p>
    <p>I founded Corwin Adeley International to provide effective, accelerated training that unlocks the highest levels of human potential. I am especially passionate about empowering executives and senior-level management to lead with clarity, impact, and well-being.</p>
  </div>
  <div class="btn about-btn">Read More</div>
</section>

<!-- bio -->
<section class="abs bio">
  <h2 class="abs heading bio-title" style="color:#fff"><b>Corwin</b> Adeley</h2>
  <div class="abs rule bio-rule"></div>
  <div class="abs bio-copy">
    <p>As a top leader, you deserve an elite partnership designed exclusively for you—especially when you need a woman you can count on.</p>
    <p>With a perspective rooted in both wisdom and empathy, I offer insights, intuition, and support that many male coaches simply cannot replicate. My mission is to guide high-performing leaders and their teams toward a state of peak performance defined by stress-free resilience, heightened productivity, and effortless flow.</p>
  </div>
  <div class="btn bio-btn">Read More</div>
  <div class="abs bio-frame"><div class="bio-photo" role="img" aria-label="Portrait photograph of the coach with arms crossed in an office"></div></div>
</section>

<!-- benefits -->
<h2 class="abs heading benefits-title"><b>Core Benefits of</b><br>Elite Coaching for Leaders</h2>
<p class="abs benefits-sub">Elite coaching provides a confidential, strategic partnership designed to elevate the performance of top executives and their organizations.</p>

<svg class="abs benefit" style="left:123px" viewBox="0 0 144 144" aria-hidden="true"><circle cx="72" cy="72" r="68" fill="#fff" stroke="#c9a36a" stroke-width="4"/><circle cx="72" cy="72" r="52" fill="#a57a3f"/><rect x="52" y="60" width="8" height="26" fill="#fff"/><rect x="66" y="50" width="8" height="36" fill="#fff"/><rect x="80" y="66" width="8" height="20" fill="#fff"/><circle cx="90" cy="86" r="7" fill="none" stroke="#fff" stroke-width="3"/></svg>
<svg class="abs benefit" style="left:393px" viewBox="0 0 144 144" aria-hidden="true"><circle cx="72" cy="72" r="68" fill="#fff" stroke="#c9a36a" stroke-width="4"/><circle cx="72" cy="72" r="52" fill="#a57a3f"/><circle cx="72" cy="58" r="8" fill="#fff"/><circle cx="54" cy="82" r="6" fill="#fff"/><circle cx="90" cy="82" r="6" fill="#fff"/><path d="M72 66V76M72 76L54 82M72 76L90 82" stroke="#fff" stroke-width="3"/></svg>
<svg class="abs benefit" style="left:664px" viewBox="0 0 144 144" aria-hidden="true"><circle cx="72" cy="72" r="68" fill="#fff" stroke="#c9a36a" stroke-width="4"/><circle cx="72" cy="72" r="52" fill="#a57a3f"/><circle cx="72" cy="56" r="8" fill="none" stroke="#fff" stroke-width="3"/><circle cx="58" cy="78" r="6" fill="#fff"/><circle cx="86" cy="78" r="6" fill="#fff"/><path d="M48 94q10-10 20 0M76 94q10-10 20 0" fill="none" stroke="#fff" stroke-width="3"/></svg>
<svg class="abs benefit" style="left:933px" viewBox="0 0 144 144" aria-hidden="true"><circle cx="72" cy="72" r="68" fill="#fff" stroke="#c9a36a" stroke-width="4"/><circle cx="72" cy="72" r="52" fill="#a57a3f"/><rect x="56" y="74" width="7" height="16" fill="#fff"/><rect x="68" y="66" width="7" height="24" fill="#fff"/><rect x="80" y="58" width="7" height="32" fill="#fff"/><path d="M54 64L70 54L86 48" fill="none" stroke="#fff" stroke-width="3"/></svg>

<p class="abs benefit-label" style="left:85px">Exclusivity and Tailored<br>Strategies</p>
<p class="abs benefit-label" style="left:355px">Strategic<br>Decision-Making</p>
<p class="abs benefit-label" style="left:626px">Leadership<br>Development</p>
<p class="abs benefit-label" style="left:895px">Navigating Organizational<br>Challenges</p>

<!-- cta -->
<section class="abs cta">
  <h2 class="abs heading cta-title" style="color:#fff">Elite Leadership is the Secret to<br><b>Lasting Organization Success...</b></h2>
  <div class="abs rule cta-rule"></div>
  <p class="abs cta-copy">Experience transformative results with a bespoke roadmap, dedicated one-on-one guidance, and confidential, high-impact strategies tailored to your unique vision.</p>
  <div class="btn cta-btn">Book a Discovery Call</div>
</section>

<!-- faq -->
<h2 class="abs heading faq-title">FAQ's</h2>
<div class="abs rule faq-rule"></div>
<div class="abs faq-item" style="top:3444px">Who is Elite Leadership for?<span class="toggle">+</span></div>
<div class="abs faq-item" style="top:3513px">How is Elite Leadership different from coaching?<span class="toggle">+</span></div>
<div class="abs faq-item faq-open" style="top:3580px">What can I expect from the initial consultation?<span class="toggle">−</span><p class="answer">A confidential discussion to explore your goals, challenges, and whether the program aligns with your leadership journey.</p></div>
<div class="abs faq-item" style="top:3719px">How long does the process take?<span class="toggle">+</span></div>
<div class="btn faq-btn">View More</div>

<!-- footer -->
<svg class="abs footer-curve" viewBox="0 0 1200 140" aria-hidden="true">
  <path d="M0 120 Q600 -40 1200 120 L1200 140 L0 140Z" fill="#050505"/>
  <path d="M0 108 Q600 -50 1200 108" fill="none" stroke="url(#goldBand)" stroke-width="16"/>
</svg>
<footer class="abs footer">
  <div class="abs footer-brand"><span class="brand-dot"></span>Corwin Adeley</div>
  <nav class="abs footer-nav"><span>Coaching</span><span>Retreats</span><span>About</span><span>Insights</span><span>Contact Us</span></nav>
  <div class="abs footer-line" style="top:229px"></div>
  <div class="abs contact" style="left:210px"><span class="contact-icon"><svg width="18" height="18" viewBox="0 0 24 24"><path d="M6.6 10.8a15 15 0 006.6 6.6l2.2-2.2a1 1 0 011-.25 11 11 0 003.5.56 1 1 0 011 1V20a1 1 0 01-1 1A17 17 0 013 4a1 1 0 011-1h3.5a1 1 0 011 1 11 11 0 00.56 3.5 1 1 0 01-.25 1z" fill="#fff"/></svg></span><div><strong>PHONE:</strong><br>+1 555 0142 7788</div></div>
  <div class="abs contact" style="left:450px"><span class="contact-icon"><svg width="18" height="14" viewBox="0 0 24 18"><rect x="1" y="1" width="22" height="16" rx="2" fill="#fff"/><path d="M1 2l11 8 11-8" fill="none" stroke="#a57a3f" stroke-width="2"/></svg></span><div><strong>E-MAIL:</strong><br>hello@corwinadeley.com</div></div>
  <div class="abs contact" style="left:767px"><span class="contact-icon"><svg width="14" height="20" viewBox="0 0 14 20"><path d="M7 0a7 7 0 00-7 7c0 5 7 13 7 13s7-8 7-13a7 7 0 00-7-7z" fill="#fff"/><circle cx="7" cy="7" r="2.5" fill="#a57a3f"/></svg></span><div><strong>ADDRESS:</strong><br>14 Harbourview Lane Marlow<br>Bay NSW 2999 Australia</div></div>
  <div class="abs footer-line" style="top:393px"></div>
  <p class="abs copyright">Copyright © 2025. All rights reserved.</p>
  <div class="abs social" aria-label="Social media links"><span></span><span></span><span></span><span></span></div>
</footer>

</body>
</html>
```